Web Design for a Biotech Consulting Firm

We need a web site design for a new business based in Philadelphia called Verantel Dx. This is a consulting firm that will serve medical diagnostics industry, which is part of the life science/healthcare industry focusing on developing and marketing products that help in early detection, monitoring or management of diseases. Our consulting firm will help medical diagnostic companies to overcome key challenges in designing, evaluating and marketing new products.Our company name is Verantel Dx. Verantel is Latin word for "something" Dx represents diagnostics. The idea behind the name is that we help companies to transform the original, early product ideas ("nothing") into "something"; which is a product with full clinical utility that will help to improve health and well-being.The web site should use the visual feel of the logo (attached), be modern, simple and clean looking and represent creativity, innovation, scientific thinking and progress.
Updates

Wix Design is acceptable

Industry/Entity Type

Biotechnology

Coding

Coded - Design and coding required

Number of Pages Required

1 page

Font styles to use
Sans Serif

Requirements
Must have
• simple, clean look couple of pages
Should not have
• a lot of pages

```html
<!DOCTYPE html>
<html lang="en">
<head>
<meta charset="utf-8">
<title>Verantel Dx</title>
<link href="https://fonts.googleapis.com/css2?family=Figtree:wght@400;500&family=Lato:wght@400;700&display=swap" rel="stylesheet">
<style>
:root{
  --blue:#1e86f0;
  --ink:#1d1d1f;
  --text:#555a60;
  --light:#f4f4f5;
  --footer:#2b303b;
  --white:#ffffff;
}
*{box-sizing:border-box;margin:0;padding:0}
html,body{width:1200px;height:2573px;overflow:hidden}
body{position:relative;font-family:"Lato",sans-serif;color:var(--text);background:var(--white)}
.abs{position:absolute}
.head{font-family:"Figtree",sans-serif;font-weight:400;color:var(--ink)}
.head span{color:var(--blue)}
.brand{position:absolute;font-family:"Lato",sans-serif;font-size:17px;font-weight:400;white-space:nowrap}
.nav{position:absolute;top:43px;left:497px;display:flex;gap:27px;font-size:14px;color:#555;letter-spacing:.3px}
.nav .active{color:var(--blue)}
.btn{position:absolute;display:flex;align-items:center;justify-content:center;font-family:"Figtree",sans-serif;font-size:17px;letter-spacing:.5px}
.btn.solid{background:var(--blue);color:var(--white)}
.btn.outline{border:2px solid var(--blue);color:var(--blue)}
.hero{left:0;top:104px;width:1200px;height:552px;background:linear-gradient(120deg,#3a4250 0%,#5b6470 40%,#4a5260 70%,#2e3540 100%)}
.hero h1{position:absolute;top:210px;width:100%;text-align:center;font-family:"Figtree",sans-serif;font-weight:400;font-size:51px;color:var(--white)}
.hero p{position:absolute;top:294px;left:212px;width:776px;text-align:center;color:var(--white);font-size:17.5px;line-height:29px}
.body-copy{font-size:14px;line-height:25px}
.services-band{left:0;top:1198px;width:1200px;height:229px;background:var(--light)}
.tile{position:absolute;top:1427px;width:400px;height:313px;display:flex;flex-direction:column;align-items:center;justify-content:center;color:var(--white)}
.tile-photo{position:absolute;inset:0}
.tile-content{position:relative;display:flex;flex-direction:column;align-items:center}
.tile-mark{width:70px;height:70px;border-radius:50%}
.tile h3{font-family:"Figtree",sans-serif;font-weight:500;font-size:19px;letter-spacing:.3px;margin-top:22px}
.tile p{font-size:13.5px;line-height:25px;text-align:center;width:320px;margin-top:10px}
.news-img{position:absolute;width:208px;height:156px}
.news-date{font-size:14px;color:#555}
.news-title{font-family:"Figtree",sans-serif;font-size:16px;color:var(--blue)}
.news-rule{width:28px;height:1px;background:#bbb}
.footer{left:0;top:2208px;width:1200px;height:365px;background:var(--footer);color:var(--white)}
.footer h4{font-family:"Figtree",sans-serif;font-weight:400;font-size:21px}
.footer li{list-style:none;font-size:14px;height:38px;display:flex;align-items:center;gap:11px}
.dot{width:7px;height:7px;border-radius:50%;background:var(--white)}
.sq{width:9px;height:9px;background:var(--white)}
</style>
</head>
<body>

<!-- Header -->
<div class="brand" style="left:79px;top:41px;color:var(--ink)">Verantel Dx</div>
<nav class="nav">
  <span class="active">HOME</span><span>ABOUT</span><span>SERVICES</span><span>NEWS</span><span>CONTACT</span>
</nav>
<div class="btn solid" style="left:904px;top:25px;width:219px;height:52px">GET A FREE QUOTE</div>

<!-- Hero -->
<section class="abs hero" role="img" aria-label="Photo of clinicians talking around a laptop">
  <h1>Lorem Ipsum is simply dummy.</h1>
  <p>Lorem Ipsum is simply dummy text of the printing and typesetting industry. Lorem Ipsum has been the industry's standard dummy text ever since the 1500s, when an unknown.</p>
</section>

<!-- Welcome -->
<h2 class="abs head" style="left:79px;top:748px;font-size:36px">Welcome to Verantel <span>Dx</span></h2>
<div class="abs body-copy" style="left:79px;top:814px;width:448px">
  <p>Lorem Ipsum is simply dummy text of the printing and typesetting industry. Lorem Ipsum has been the industry's standard dummy text ever since the 1500s, when an unknown printer took a galley of type and scrambled it to make a type specimen book.</p>
  <p style="margin-top:13px">It has survived not only five centuries, but also the leap into electronic typesetting, remaining essentially unchanged. It was popularised in the 1960s with the release of Letraset sheets containing Lorem Ipsm.</p>
</div>
<div class="btn solid" style="left:77px;top:1032px;width:188px;height:52px">KNOW MORE</div>
<div class="btn outline" style="left:285px;top:1032px;width:188px;height:52px">CONTACT US</div>
<div class="abs" style="left:654px;top:747px;width:469px;height:312px;border:4px solid var(--blue)"></div>
<div class="abs" role="img" aria-label="Photo of a scientist using a holographic medical display" style="left:623px;top:789px;width:458px;height:312px;background:linear-gradient(135deg,#3f7c92 0%,#8fc0d6 45%,#c9e2ee 70%,#6f9fbb 100%)"></div>

<!-- Services -->
<div class="abs services-band"></div>
<h2 class="abs head" style="left:0;top:1253px;width:1200px;text-align:center;font-size:36px">Our <span>Services</span></h2>
<p class="abs body-copy" style="left:268px;top:1315px;width:664px;text-align:center">Lorem Ipsum is simply dummy text of the printing and typesetting industry. Lorem Ipsum has been the industry's standard dummy text ever since the 1500s, when an unknown printer took a galley.</p>

<div class="tile" style="left:0">
  <div class="tile-photo" role="img" aria-label="Photo of a microscope and a clinician with a tablet" style="background:linear-gradient(120deg,#3c3c3c,#6a6a6a 60%,#4a4a4a)"></div>
  <div class="tile-content" style="margin-top:40px">
    <div class="tile-mark" style="border:3px solid var(--blue)"></div>
    <h3>DEVELOPMENT</h3>
  </div>
</div>
<div class="tile" style="left:400px">
  <div class="tile-photo" role="img" aria-label="Photo of surgeons under a blue overlay" style="background:#3590f2"></div>
  <div class="tile-content">
    <div class="tile-mark" style="border:2px solid var(--white)"></div>
    <h3>MARKETING</h3>
    <p>Lorem Ipsum is simply dummy text of the printing and typesetting indust Lorem Ipsum has been the industry's standard dummy text ever.</p>
  </div>
</div>
<div class="tile" style="left:800px">
  <div class="tile-photo" role="img" aria-label="Photo of a doctor beside a patient record screen" style="background:linear-gradient(120deg,#4a4a4a,#6b6b6b 50%,#3e3e3e)"></div>
  <div class="tile-content" style="margin-top:40px">
    <div class="tile-mark" style="border:3px solid var(--blue)"></div>
    <h3>MONITORING</h3>
  </div>
</div>

<!-- News -->
<h2 class="abs head" style="left:0;top:1790px;width:1200px;text-align:center;font-size:36px">Latest <span>News</span></h2>

<div class="news-img" role="img" aria-label="Photo of two nurses reviewing a screen" style="left:77px;top:1870px;background:linear-gradient(135deg,#c8d3de,#4f78a8 60%,#2c3a55)"></div>
<div class="abs" style="left:315px;top:1878px;width:245px">
  <div class="news-date">20 JUN 2019</div>
  <div class="news-title" style="margin-top:11px">Lorem Ipsum is simply dummy.</div>
  <div class="news-rule" style="margin-top:15px"></div>
  <p class="body-copy" style="margin-top:10px">Lorem Ipsum is simply dummy text of the printing and typesetting industry Lorem Ipsum has been.</p>
</div>

<div class="news-img" role="img" aria-label="Photo of a doctor writing notes beside a laptop" style="left:622px;top:1870px;background:linear-gradient(135deg,#e8ecef,#b9c2cb 55%,#59626d)"></div>
<div class="abs" style="left:859px;top:1878px;width:245px">
  <div class="news-date">20 JUN 2019</div>
  <div class="news-title" style="margin-top:11px">Lorem Ipsum is simply dummy.</div>
  <div class="news-rule" style="margin-top:15px"></div>
  <p class="body-copy" style="margin-top:10px">Lorem Ipsum is simply dummy text of the printing and typesetting industry Lorem Ipsum has been.</p>
</div>

<div class="btn solid" style="left:506px;top:2071px;width:188px;height:52px">EXPLORE MORE</div>

<!-- Footer -->
<footer class="abs footer">
  <div class="brand" style="left:79px;top:93px;color:var(--white)">Verantel Dx</div>
  <p class="abs" style="left:79px;top:163px;width:232px;font-size:14px;line-height:25px">Lorem Ipsum is simply dummy text of the printing and typesetting.</p>

  <h4 class="abs" style="left:379px;top:62px">Sitemap</h4>
  <ul class="abs" style="left:379px;top:97px">
    <li><span class="dot"></span>About us</li>
    <li><span class="dot"></span>Services</li>
    <li><span class="dot"></span>Latest News</li>
    <li><span class="dot"></span>Contact</li>
  </ul>

  <h4 class="abs" style="left:596px;top:62px">Contact Info</h4>
  <div class="abs" style="left:596px;top:105px;font-size:14px;line-height:25px;width:205px">
    <b>ADDRESS :</b><br>Lorem Ipsum is simply dummy text of the printing and typeset.
    <div style="margin-top:12px"><b>PHONE :</b><br>123 456 7890</div>
  </div>

  <h4 class="abs" style="left:885px;top:62px">Social Media</h4>
  <ul class="abs" style="left:884px;top:97px">
    <li><span class="sq"></span>&nbsp;Pagebook</li>
    <li><span class="sq"></span>&nbsp;Chirper</li>
    <li><span class="sq"></span>&nbsp;Linkwork</li>
    <li><span class="sq"></span>&nbsp;Circles+</li>
  </ul>

  <p class="abs" style="left:0;top:327px;width:1200px;text-align:center;font-size:14px">©Verantel Dx. 2019 - All Rights Reserved.</p>
</footer>

</body>
</html>
```